BUSINESS CARD - HALLORAN FIELD SERVICES

I would like to create a business card for my fertilizer spreading business. I would like to incorporate my existing logo and also a description of the services offered. The business card will be given to farmers so must be kept simple but effective. It will also be left in stores so much also be eye catching in order to stand out from other cards.

Target Market(s)

FARMERS

Requirements
Must have
• FRONT OF CARD = EXISTING LOGO + "CUSTOMISED SPREADING" below the logo

REAR Of CARD = SERVICES OFFERED AND CONTACT DETAILS

- Bulk fertilizer including Lime, Gypsum, Manure & Compost
- Granular fertilizer including Single Super, Urea, Gran-am, & Custom Blends
- Modern equipment - Autosteer & Variable Rate Capable
- Friendly & Reliable Service
- Contact Gus: 0417 552 308
Nice to have
• utilize same color scheme as existing logo

```html
<!DOCTYPE html>
<html lang="en">
<head>
<meta charset="utf-8">
<title>Halloran Field Services – Business Card</title>
<link rel="stylesheet" href="https://fonts.googleapis.com/css2?family=Arimo:wght@400;700&display=swap">
<style>
  :root {
    --backdrop: #2b2b2b;
    --card-white: #ffffff;
    --brand-orange: #f7941d;
    --orange-deep: #e8861a;
    --charcoal: #4d4d4f;
    --ink-white: #ffffff;
  }
  * { box-sizing: border-box; margin: 0; padding: 0; }
  html, body {
    width: 1200px;
    height: 900px;
    overflow: hidden;
    background: var(--backdrop);
    font-family: "Arimo", Arial, sans-serif;
  }
  .canvas {
    position: relative;
    width: 1200px;
    height: 900px;
  }
  .card {
    position: absolute;
    left: 250px;
    width: 700px;
    height: 400px;
    overflow: hidden;
  }
  .card--front {
    top: 40px;
    background: var(--card-white);
  }
  .card--back {
    top: 460px;
    background: var(--brand-orange);
    color: var(--ink-white);
  }

  /* Front */
  .brand {
    position: absolute;
    left: 0;
    right: 0;
    top: 120px;
    display: flex;
    align-items: center;
    justify-content: center;
    gap: 18px;
  }
  .brand__dot {
    width: 58px;
    height: 58px;
    border-radius: 50%;
    background: var(--charcoal);
    flex: none;
  }
  .brand__name {
    color: var(--charcoal);
    font-weight: 700;
    font-size: 40px;
    letter-spacing: -0.5px;
    line-height: 1;
  }
  .brand__rule {
    position: absolute;
    left: 150px;
    right: 150px;
    top: 212px;
    height: 3px;
    background: var(--brand-orange);
  }
  .tagline {
    position: absolute;
    left: 0;
    right: 0;
    top: 250px;
    text-align: center;
    color: var(--brand-orange);
    font-size: 26px;
    letter-spacing: 3px;
  }

  /* Back */
  .back__ring {
    position: absolute;
    left: 230px;
    top: 40px;
    width: 320px;
    height: 320px;
    border-radius: 50%;
    border: 22px solid var(--orange-deep);
  }
  .services {
    position: absolute;
    left: 0;
    right: 0;
    top: 62px;
    list-style: none;
    text-align: center;
    font-size: 20px;
    line-height: 1.38;
  }
  .services__gap { margin-top: 10px; }
  .contact {
    position: absolute;
    left: 0;
    right: 0;
    top: 282px;
    text-align: center;
    font-size: 34px;
    letter-spacing: 0.5px;
  }
</style>
</head>
<body>
<main class="canvas">
  <section class="card card--front" aria-label="Front of card">
    <div class="brand">
      <span class="brand__dot" aria-hidden="true"></span>
      <h1 class="brand__name">HALLORAN FIELD SERVICES</h1>
    </div>
    <div class="brand__rule" aria-hidden="true"></div>
    <p class="tagline">CUSTOMISED SPREADING</p>
  </section>

  <section class="card card--back" aria-label="Back of card">
    <div class="back__ring" aria-hidden="true"></div>
    <ul class="services">
      <li>Bulk fertilizer including Lime, Gypsum, Manure &amp; Compost</li>
      <li>Granular fertilizer including Single Super, Urea</li>
      <li>Gran-am, &amp; Custom Blends</li>
      <li class="services__gap">Modern equipment</li>
      <li>Autosteer &amp; Variable Rate Capable</li>
      <li>Friendly &amp; Reliable Service</li>
    </ul>
    <p class="contact">Contact Gus: 0417 552 308</p>
  </section>
</main>
</body>
</html>
```